Anzeigengestaltung für eine Hausarztpraxis
Zielgruppe
Wir sind eine Hausarztpraxis mit zwei Standorten und suchen eine Ärztin oder einen Arzt zur Anstellung in der klassischen Hausarzt Medizin am Standort Erlenbrück
Aufgabenstellung
Bitte beachtet den Text im Anhang, der ist schon vorgegeben. (Anzeigentext)
Wir suchen ein ruhiges, hochwertiges Layout für eine Stellenanzeige einer Hausarztpraxis in einem historischen Gebäude.
Der Text steht im Vordergrund, das Design soll zurückhaltend, klar und wertig sein.
Bitte keine Icons, keine bunten Farben, keine verspielten Elemente.
Gerne viel Weissraum, klare Typografie, ruhige Anmutung.
Schrift: Garamond für den Fliesstext (bereits gewählt).
Das Layout soll sowohl als PDF wie auch online funktionieren.
Optional: ein sehr dezentes grafisches Element oder eine ruhige Bildanmutung (z. B. Struktur, Licht, Architekturdetail).

```html
<!DOCTYPE html>
<html lang="de">
<head>
<meta charset="utf-8">
<title>Stellenanzeige Hausarztpraxis Erlenbrück</title>
<link rel="stylesheet" href="https://fonts.googleapis.com/css2?family=EB+Garamond:wght@400;500;700;800&display=swap">
<style>
  :root{
    --dark:#252f27;
    --green:#7cc043;
    --white:#ffffff;
    --ink:#1f241f;
    --photo-wood:#9a6a3a;
    --photo-room:#d9d6cf;
    --photo-court:#b9b3a7;
  }
  *{margin:0;padding:0;box-sizing:border-box}
  html,body{width:960px;height:1200px;overflow:hidden;background:var(--white)}
  body{font-family:"EB Garamond",Garamond,serif;color:var(--ink)}
  .ad{position:relative;width:960px;height:1200px;overflow:hidden;background:var(--white)}

  .brand{position:absolute;left:28px;top:116px;display:flex;align-items:center;gap:12px}
  .brand__name{font-weight:700;font-size:34px;line-height:1.05;color:var(--dark)}
  .brand__dot{width:30px;height:30px;border-radius:50%;background:var(--green)}

  .photo{position:absolute;border-radius:50%;border:6px solid var(--white)}
  .photo--reception{left:364px;top:-12px;width:296px;height:296px;background:radial-gradient(circle at 45% 40%,#c08a52,var(--photo-wood) 60%,#6d4a28)}
  .photo--room{left:640px;top:-28px;width:336px;height:336px;background:radial-gradient(circle at 55% 40%,#f3f1ec,var(--photo-room) 60%,#8a7a66)}
  .photo--courtyard{left:628px;top:232px;width:344px;height:344px;background:linear-gradient(180deg,#eeeae3 0%,#d8d2c6 40%,var(--photo-court) 65%,#9c9486 100%)}

  .band{position:absolute;left:0;top:274px;width:650px;height:222px;background:var(--dark)}
  .headline{position:absolute;left:28px;top:302px;color:var(--white)}
  .headline__main{font-weight:800;font-size:52px;line-height:1;color:var(--green);letter-spacing:.5px}
  .headline__sub{font-weight:700;font-size:31px;line-height:1.25;margin-top:8px;letter-spacing:.3px}
  .headline__claim{font-size:18.5px;margin-top:12px}

  .intro{position:absolute;left:28px;top:504px;font-size:19.6px;line-height:24px;white-space:nowrap}

  .pillar{position:absolute;border-radius:50%;text-align:center;display:flex;flex-direction:column;align-items:center}
  .pillar__title{font-weight:800;font-size:29px;line-height:1.08;color:var(--green)}
  .pillar__text{margin-top:10px;white-space:nowrap}
  .pillar--team{left:16px;top:736px;width:300px;height:300px;background:var(--dark);color:var(--white);padding:36px 10px 0}
  .pillar--team .pillar__text{font-size:19px;line-height:23px}
  .pillar--time{left:324px;top:724px;width:300px;height:300px;background:var(--green);color:var(--dark);padding:46px 10px 0}
  .pillar--time .pillar__title{color:var(--dark)}
  .pillar--time .pillar__text{font-size:17px;line-height:21px}
  .pillar--more{left:644px;top:740px;width:304px;height:304px;background:var(--dark);color:var(--white);padding:40px 10px 0}
  .pillar--more .pillar__text{font-size:14.6px;line-height:18.4px;margin-top:10px}

  .closing{position:absolute;left:30px;top:1064px;font-size:19.5px;line-height:23px;white-space:nowrap}
  .contact{position:absolute;left:522px;top:1066px;list-style:none;font-size:19.5px;line-height:26px;white-space:nowrap}
  .contact li{display:flex;align-items:center;gap:8px}
  .contact svg{width:18px;height:18px;flex:none}

  .rule{position:absolute;left:0;top:1162px;width:960px;height:6px;background:var(--green)}
  .footer-band{position:absolute;left:0;top:1168px;width:960px;height:32px;background:var(--dark)}
</style>
</head>
<body>
<main class="ad">
  <div class="brand">
    <span class="brand__name">Arztpraxis<br>Lebensquell</span>
    <span class="brand__dot"></span>
  </div>

  <div class="band"></div>
  <div class="photo photo--reception" role="img" aria-label="Foto: Empfang mit Holztheke und altem Apothekerschrank"></div>
  <div class="photo photo--room" role="img" aria-label="Foto: heller Behandlungsraum mit Liege und Schreibtisch"></div>
  <div class="photo photo--courtyard" role="img" aria-label="Foto: historisches Praxisgebäude mit Innenhof und Steinbrunnen"></div>

  <header class="headline">
    <h1 class="headline__main">HAUSARZTMEDIZIN</h1>
    <p class="headline__sub">MIT TIEFE – DORT, WO MAN NOCH<br>ECHTE GRUNDVERSORGUNG LEBT</p>
    <p class="headline__claim">Ein Ort, der trägt. Ein Team, das bleibt. Eine Arbeit, die Wertschätzung hat.</p>
  </header>

  <section class="intro">
    <p>Manche Orte verändern die Art, wie man arbeitet.<br>
    Unsere Praxis in Erlenbrück ist so ein Ort.<br>
    In einem historischen Gebäude gelegen, mit grosszügigem Ambiente, warmen<br>
    Vertäfelungen und kunstvoller Wandbemalung, entstehen hier Behandlungsräume von<br>
    Ruhe und Würde. Kein steriler Praxisalltag, sondern ein Ort, der Gespräche trägt und<br>
    medizinische Arbeit unterstützt.<br>
    Für diesen besonderen Ort suchen wir eine Hausärztin oder einen Hausarzt, die oder der<br>
    nicht einfach einen Arbeitsplatz sucht, sondern einen Platz, an dem<br>
    Medizin menschlich sein darf.</p>
  </section>

  <section class="pillar pillar--team">
    <h2 class="pillar__title">EIN TEAM<br>MIT HALTUNG</h2>
    <p class="pillar__text">Sie arbeiten in einem<br>freundlichen, über Jahre<br>gewachsenen Team mit hoher<br>personeller Kontinuität<br>und geringer Fluktuation.</p>
  </section>

  <section class="pillar pillar--time">
    <h2 class="pillar__title">ZEIT FÜR<br>GUTE MEDIZIN</h2>
    <p class="pillar__text">Unsere Patientinnen und<br>Patienten sind überwiegend gut bis<br>sehr gut situiert, wertschätzend und<br>therapieoffen. Das ermöglicht ruhiges,<br>strukturiertes Arbeiten mit Fokus auf<br>Qualität, Beziehung und nachhaltige<br>Behandlung.</p>
  </section>

  <section class="pillar pillar--more">
    <h2 class="pillar__title">UND SONST?</h2>
    <p class="pillar__text">Der Praxisalltag ist klar strukturiert, ruhig<br>und verlässlich. Geregelte und in<br>Abstimmung flexible Arbeitszeiten ohne<br>Wochenend- oder Nachtdienste, eine sehr<br>gute leistungsbezogene Vergütung sowie<br>ein respektvoller, wertschätzender<br>Umgang auf Augenhöhe schaffen ein<br>Umfeld, in dem man sich auf die<br>medizinische Arbeit konzentrieren<br>und langfristig wohlfühlen kann.</p>
  </section>

  <p class="closing">Wir freuen uns über eine unkomplizierte Kontaktaufnahme<br>per E-Mail oder Telefon – gerne auch ganz unverbindlich und<br>ohne vollständige Bewerbungsunterlagen.</p>

  <ul class="contact">
    <li><svg viewBox="0 0 20 20"><rect x="1" y="4" width="18" height="13" rx="1.5" fill="var(--green)"/><path d="M2 5l8 6 8-6" fill="none" stroke="#fff" stroke-width="1.6"/></svg>Helga.Weissmoor@praxis-lebensquell.ch</li>
    <li><svg viewBox="0 0 20 20"><path d="M10 1a6.5 6.5 0 0 0-6.5 6.5C3.5 12.5 10 19 10 19s6.5-6.5 6.5-11.5A6.5 6.5 0 0 0 10 1z" fill="var(--green)"/><circle cx="10" cy="7.5" r="2.4" fill="#fff"/></svg>Arztpraxis Lebensquell Lindenweg 7 4799 Erlenbrück</li>
    <li><svg viewBox="0 0 20 20"><path d="M5 2l3 3.5-1.6 2.2a10 10 0 0 0 5.9 5.9l2.2-1.6L18 15l-1.6 2.6C9.5 17.5 2.5 10.5 2.4 3.6z" fill="var(--green)"/></svg>Tel: 0621234567</li>
  </ul>

  <div class="rule"></div>
  <div class="footer-band"></div>
</main>
</body>
</html>
```